Moonridge Real Estate Sign

We are in the process of rebranding our business and need a new For Sale \ Sold sign.
We're a prestige real estate agency and therefore require a really stylish sign.
I've uploaded the following files
1. The new company logo
2. "sample sign.jpg" which shows the type of sign we would like. It is a metal sign with a top panel and bottom panel.
3. Our previous sign "previous sign.jpg" if you're interested in seeing it.
The sign must be black with white text.
Our thoughts are that the top panel (refer to sample sign) would contain the text "For Sale" or "Sold". These would be two separate panels which are interchangeable and could be screwed in place.
The bottom panel would not contain any photos like the sample. However, it may contain our logo and my contact details etc.
The sign is 900mm wide x 1200mm high.
My details are:
Name: Gerald Fenwick
Web: www.mrrealestate.com.au
Email: sales@mrrealestate.com.au
Phone: 0491 806 357

```html
<!DOCTYPE html>
<html lang="en">
<head>
<meta charset="utf-8">
<title>Moonridge Real Estate – For Sale Sign</title>
<link rel="stylesheet" href="https://fonts.googleapis.com/css2?family=Lato:wght@700&family=Montserrat:wght@500;600;700&display=swap">
<style>
  :root {
    --backdrop: #eceeea;
    --sign-black: #1c1c1c;
    --panel-black: #222222;
    --heading-ink: #e4e4e4;
    --band-light: #f2f2f2;
    --skyline: #d4d4d4;
    --lower-grey: #dadada;
    --ink: #1a1a1a;
    --ink-soft: #333333;
    --white: #ffffff;
  }
  * { margin: 0; padding: 0; box-sizing: border-box; }
  html, body {
    width: 1019px;
    height: 1200px;
    overflow: hidden;
    background: var(--backdrop);
  }
  .canvas {
    position: relative;
    width: 1019px;
    height: 1200px;
  }
  .sign {
    position: absolute;
    left: 37px;
    top: 246px;
    width: 945px;
    height: 708px;
    background: var(--sign-black);
    padding: 0 12px;
  }
  .heading-panel {
    height: 207px;
    background: var(--panel-black);
    display: flex;
    align-items: center;
    justify-content: center;
  }
  .heading-panel h1 {
    font-family: "Lato", sans-serif;
    font-weight: 700;
    font-size: 136px;
    letter-spacing: 6px;
    word-spacing: 28px;
    color: var(--heading-ink);
    line-height: 1;
  }
  .details-panel {
    margin-top: 3px;
    height: 498px;
    background: var(--lower-grey);
    display: flex;
    flex-direction: column;
  }
  .brand-band {
    position: relative;
    height: 196px;
    background: var(--band-light);
    overflow: hidden;
  }
  .skyline {
    position: absolute;
    inset: 40px 0 0 0;
    background: linear-gradient(180deg, var(--band-light) 0%, var(--skyline) 55%, #c9c9c9 100%);
  }
  .brand {
    position: absolute;
    left: 0;
    right: 0;
    top: 62px;
    display: flex;
    align-items: center;
    justify-content: center;
    gap: 22px;
  }
  .brand-name {
    font-family: "Montserrat", sans-serif;
    font-weight: 700;
    font-size: 52px;
    color: var(--ink);
    letter-spacing: -0.5px;
  }
  .brand-dot {
    width: 78px;
    height: 78px;
    border-radius: 50%;
    background: var(--ink);
  }
  .agent-band {
    height: 94px;
    background: var(--panel-black);
    display: flex;
    align-items: center;
    justify-content: center;
  }
  .agent-name {
    font-family: "Montserrat", sans-serif;
    font-weight: 600;
    font-size: 42px;
    color: var(--white);
    margin-left: -60px;
  }
  .contact {
    flex: 1;
    display: flex;
    flex-direction: column;
    align-items: center;
    padding-top: 16px;
  }
  .phone {
    font-family: "Montserrat", sans-serif;
    font-weight: 700;
    font-size: 82px;
    color: var(--ink);
    line-height: 1.05;
    letter-spacing: -1px;
  }
  .email {
    font-family: "Montserrat", sans-serif;
    font-weight: 500;
    font-size: 24px;
    letter-spacing: 3px;
    color: var(--ink-soft);
    margin-top: 6px;
  }
  .web {
    display: flex;
    align-items: center;
    gap: 10px;
    margin-top: 2px;
  }
  .web-rule {
    width: 62px;
    height: 3px;
    background: var(--ink);
  }
  .web-address {
    font-family: "Montserrat", sans-serif;
    font-weight: 700;
    font-size: 27px;
    letter-spacing: 1.5px;
    color: var(--ink);
  }
</style>
</head>
<body>
<main class="canvas">
  <section class="sign">
    <header class="heading-panel">
      <h1>FOR SALE</h1>
    </header>
    <div class="details-panel">
      <div class="brand-band">
        <div class="skyline" role="img" aria-label="Pale grey city skyline silhouette behind the agency name"></div>
        <div class="brand">
          <span class="brand-name">Moonridge Real Estate</span>
          <span class="brand-dot"></span>
        </div>
      </div>
      <div class="agent-band">
        <p class="agent-name">Gerald Fenwick</p>
      </div>
      <div class="contact">
        <p class="phone">Ph:0491 806 357</p>
        <p class="email">Email: sales@mrrealestate.com.au</p>
        <p class="web">
          <span class="web-rule"></span>
          <span class="web-address">www.mrrealestate.com.au</span>
          <span class="web-rule"></span>
        </p>
      </div>
    </div>
  </section>
</main>
</body>
</html>
```